Fast quick flyer for Merchant Growth Fair

I am an information security consultant that needs to have a flyer and QUICK!!!
I need to get it to the printer today to have if done by monday. Quick turnaound.
I don't need the most amazing flyer but something that will capture their attention and offer them 40% off my base rate.
Updates

Here's some slight updates to the text, can you update and incorporate (PS: For some reason, when I initially put in Vantrel Systems, a " (quote) showed up, it's an apostrophe ( Vantrel Systems): Text: Vantrel Systems is the information security department for small and mid-sized businesses. Leveraging our 20+ years of information security experience, we will bring you the same level of service found at Pinnacle 300 companies. Small and mid-sized companies are often the target of malicious activity because they tend to lack the expertise to properly secure their environments. Now you can have your very own information security department at a fraction of the cost of a full time staff. Our typical rate for our premium offering: Guardline Plus is $5000/month based on a signed one year commitment. But for expo attendees, we are offering a special discount. As an expo attendee, you are eligible for a 40% discount. Guardline Plus for expo attendees will be $3000/month based on a signed one year commitment. Why put your company and your business at risk. Vantrel Systems is here to secure your company's future! Contact us now for more information: Leon Whitcombe Vantrel Systems "The information security department of small and mid-sized companies" 555-318-7292 info@vantrelsys.example http://www.vantrelsys.example

Also, this is going to be a 6x9 heavy stock postcard

Addition: Promo Code: GrowthFair 2014

Target Market(s)

Small businesses with a small IT department that can't afford to hire a full time IT Security Staff. We are the outsourced Information Security group

Industry/Entity Type

Small Business

Colors

Designer to choose colors to be used in the design.

Requirements
Must have
• Sell the idea that they need to take security serious and that we are the ones to do the job

Should stress that because they are attendees of the Merchant Growth Fair, they are eligible to get a 40% discount on our standard rate

```html
<!DOCTYPE html>
<html lang="en">
<head>
<meta charset="utf-8">
<title>Vantrel Systems – Merchant Growth Fair Postcard</title>
<link rel="stylesheet" href="https://fonts.googleapis.com/css2?family=Roboto:wght@400;500;700;900&display=swap">
<style>
  :root {
    --ink: #111418;
    --brand-navy: #1f2d57;
    --white: #ffffff;
    --bg-light: #f4f6f8;
    --bg-mid: #c9ced4;
    --bg-dark: #5c6470;
    --bg-deep: #3a404a;
    --glow: #f3b45a;
    --badge-outer: #3b3d40;
    --badge-inner: #55585c;
    --badge-ring: #8a8d91;
  }
  * { margin: 0; padding: 0; box-sizing: border-box; }
  html, body { width: 1200px; height: 846px; overflow: hidden; background: var(--white); }
  body { font-family: "Roboto", Arial, sans-serif; color: var(--ink); }

  .postcard { position: relative; width: 1200px; height: 846px; overflow: hidden; }

  .hero-photo {
    position: absolute; inset: 0;
    background:
      radial-gradient(ellipse 220px 160px at 640px 360px, rgba(243,180,90,0.45), rgba(243,180,90,0) 70%),
      radial-gradient(ellipse 520px 620px at 900px 520px, rgba(58,64,74,0.55), rgba(58,64,74,0) 75%),
      linear-gradient(90deg, var(--bg-light) 0%, var(--bg-light) 28%, var(--bg-mid) 52%, var(--bg-dark) 78%, var(--bg-deep) 100%);
  }

  .brand { position: absolute; left: 62px; top: 70px; display: flex; align-items: center; gap: 18px; }
  .brand-mark { width: 62px; height: 62px; background: var(--brand-navy); }
  .brand-name { font-size: 44px; font-weight: 700; color: var(--brand-navy); letter-spacing: 0.5px; }

  .offer-badge { position: absolute; left: 958px; top: 4px; width: 196px; height: 196px; }
  .offer-badge svg { position: absolute; inset: 0; }
  .offer-text { position: absolute; inset: 0; display: flex; flex-direction: column; align-items: center; justify-content: center; color: var(--white); text-align: center; }
  .offer-label { font-size: 13px; font-weight: 700; }
  .offer-value { font-size: 46px; font-weight: 900; line-height: 1.05; }
  .offer-regular { font-size: 9px; font-weight: 500; letter-spacing: 0.3px; }

  .headline {
    position: absolute; left: 74px; top: 334px; width: 700px;
    font-size: 48px; font-weight: 500; line-height: 54px; letter-spacing: -0.3px;
  }

  .pitch {
    position: absolute; left: 90px; top: 532px; width: 650px;
    font-size: 24px; font-weight: 700; line-height: 36px;
  }

  .contact { position: absolute; left: 780px; top: 694px; color: var(--white); }
  .contact-name { font-size: 34px; font-weight: 700; line-height: 40px; }
  .contact-email { font-size: 18px; font-weight: 700; line-height: 22px; }
  .contact-phone { font-size: 43px; font-weight: 700; line-height: 46px; letter-spacing: 0.5px; }
  .contact-web { font-size: 20px; font-weight: 700; line-height: 24px; }
</style>
</head>
<body>
<main class="postcard">
  <div class="hero-photo" role="img" aria-label="Photo of a businessman touching a glowing screen surrounded by floating device icons"></div>

  <header class="brand">
    <span class="brand-mark"></span>
    <span class="brand-name">Vantrel Systems</span>
  </header>

  <div class="offer-badge">
    <svg viewBox="0 0 196 196" width="196" height="196" aria-hidden="true">
      <polygon fill="var(--badge-outer)" points="98,4 109,22 127,10 132,31 153,26 151,48 172,50 163,70 182,80 167,95 182,110 163,121 172,141 151,143 153,165 132,160 127,181 109,170 98,188 87,170 69,181 64,160 43,165 45,143 24,141 33,121 14,110 29,95 14,80 33,70 24,50 45,48 43,26 64,31 69,10 87,22"/>
      <circle cx="98" cy="96" r="66" fill="var(--badge-inner)" stroke="var(--badge-ring)" stroke-width="2"/>
    </svg>
    <div class="offer-text">
      <span class="offer-label">Special Expo Rate</span>
      <span class="offer-value">40% OFF</span>
      <span class="offer-regular">REGULAR PRICE $5,000.00</span>
    </div>
  </div>

  <h1 class="headline">Information security department for small and mid-sized businesses</h1>

  <p class="pitch">Small companies are targets because they lack the expertise at information security that large companies have.&nbsp; We have over 20 years of information security experience and we can leverage our expertise to give small companies the same level of security experience that Pinnacle 300 companies have.</p>

  <address class="contact" style="font-style: normal;">
    <div class="contact-name">Leon Whitcombe</div>
    <div class="contact-email">leon.whitcombe@vantrelsys.example</div>
    <div class="contact-phone">555-318-7292</div>
    <div class="contact-web">http://www.vantrelsys.example</div>
  </address>
</main>
</body>
</html>
```